Home Remodeling company needs a business card design

we need a business card design for home remodeling company in hamilton county, indiana USA. we offers a wide range of construction services including whole house renovations, Design and Build Basements and Kitchen and Bathroom Remodeling . we would like to see designs for both site of business card that use the same color of the company logo and also including all information below :
1- Karim Feltous CEO / General Contractor
2- all company contacts Telephone numbers ( 1-888-DULOM-47 ) ( 317-555-0193) email address ( info@dulomhome.com) website ( www.dulomhome.com ) and social media logos (Facebook- twitter- google plus )
3- company logo
4- licensed . insured . bonded

```html
<!DOCTYPE html>
<html lang="en">
<head>
<meta charset="utf-8">
<title>Dulom Home Remodeling – Business Card</title>
<link rel="stylesheet" href="https://fonts.googleapis.com/css2?family=Ubuntu:wght@400;500&display=swap">
<style>
  :root {
    --brand-red: #c8323a;
    --charcoal: #3a3a3c;
    --slate: #6d6e70;
    --paper: #ffffff;
    --backdrop: #e9eaeb;
  }
  * { box-sizing: border-box; margin: 0; padding: 0; }
  html, body {
    width: 1189px; height: 1200px; overflow: hidden;
    background: var(--backdrop);
  }
  .card {
    position: absolute; left: 140px; width: 917px; height: 524px;
    overflow: hidden;
    box-shadow: 0 4px 10px rgba(0,0,0,0.25);
  }
  .card--front { top: 45px; background: var(--paper); }
  .card--back { top: 624px; background: var(--brand-red); }

  .brand {
    position: absolute; left: 0; width: 100%;
    display: flex; align-items: center; justify-content: center; gap: 22px;
  }
  .brand__square { width: 30px; height: 30px; background: var(--brand-red); flex: none; }
  .brand__name {
    font-family: "Ubuntu", sans-serif; font-weight: 500;
    font-size: 118px; line-height: 1; color: var(--charcoal);
  }
  .card--front .brand { top: 50px; height: 150px; }
  .card--back .brand { top: 187px; height: 150px; }
  .card--back .brand__square { background: var(--paper); }
  .card--back .brand__name { color: var(--paper); font-size: 128px; }

  .social-links { position: absolute; left: 119px; top: 232px; display: flex; gap: 24px; }
  .social-links span { width: 30px; height: 28px; border-radius: 3px; }
  .social-links span:nth-child(1) { background: #d0413a; }
  .social-links span:nth-child(2) { background: #3b5c9a; }
  .social-links span:nth-child(3) { background: #2fa4df; }

  .credentials {
    position: absolute; right: 117px; top: 227px;
    font-family: "Ubuntu", sans-serif; font-size: 32px; color: var(--slate);
  }

  .divider-band {
    position: absolute; left: 0; top: 288px; width: 100%; height: 11px;
    background: var(--charcoal);
  }
  .contact-panel {
    position: absolute; left: 0; top: 299px; width: 100%; height: 225px;
    background: var(--brand-red); color: var(--paper);
    font-family: "Ubuntu", sans-serif;
  }
  .person { position: absolute; left: 49px; top: 46px; }
  .person__name { font-size: 50px; line-height: 1.1; }
  .person__role { font-size: 30px; font-weight: 500; line-height: 1.3; margin-top: 6px; }
  .panel-rule {
    position: absolute; left: 466px; top: 21px; width: 3px; height: 168px;
    background: var(--paper);
  }
  .contact-list { position: absolute; left: 531px; top: 37px; list-style: none; }
  .contact-list li {
    display: flex; align-items: center; gap: 16px;
    font-size: 28px; font-weight: 500; height: 38px;
  }
  .contact-list svg { width: 18px; height: 18px; flex: none; }
</style>
</head>
<body>

<section class="card card--front" aria-label="Business card front">
  <div class="brand">
    <span class="brand__square"></span>
    <span class="brand__name">Dulom</span>
  </div>

  <div class="social-links" aria-label="Social media">
    <span></span><span></span><span></span>
  </div>
  <p class="credentials">licensed .insured . bonded</p>

  <div class="divider-band"></div>

  <div class="contact-panel">
    <div class="person">
      <p class="person__name">Karim Feltous</p>
      <p class="person__role">General Contractor<br>CEO</p>
    </div>
    <div class="panel-rule"></div>
    <ul class="contact-list">
      <li>
        <svg viewBox="0 0 18 18"><rect width="18" height="18" rx="2" fill="#fff"/><path d="M6 3.5l2 2.5-1.2 1.4c.8 1.6 2 2.8 3.8 3.8L12 10l2.5 2-1.3 2.2C9 13.6 4.4 9 3.8 4.8z" fill="#c8323a"/></svg>
        1-888-DULOM-47
      </li>
      <li>
        <svg viewBox="0 0 18 18"><rect width="18" height="18" rx="2" fill="#fff"/><path d="M3 7c3-3 9-3 12 0l-1.5 1.5-2-1V6h-5v1.5l-2 1z M5 10h8v4H5z" fill="#c8323a"/></svg>
        317-555-0193
      </li>
      <li>
        <svg viewBox="0 0 18 18"><rect width="18" height="18" rx="2" fill="#fff"/><rect x="3.5" y="5" width="11" height="8" fill="none" stroke="#c8323a" stroke-width="1.4"/><path d="M3.5 5L9 9.5 14.5 5" fill="none" stroke="#c8323a" stroke-width="1.4"/></svg>
        info@dulomhome.com
      </li>
      <li>
        <svg viewBox="0 0 18 18"><rect width="18" height="18" rx="2" fill="#fff"/><circle cx="9" cy="9" r="5.5" fill="none" stroke="#c8323a" stroke-width="1.4"/><path d="M3.5 9h11M9 3.5c-2.5 3-2.5 8 0 11M9 3.5c2.5 3 2.5 8 0 11" fill="none" stroke="#c8323a" stroke-width="1.1"/></svg>
        www.dulomhome.com
      </li>
    </ul>
  </div>
</section>

<section class="card card--back" aria-label="Business card back">
  <div class="brand">
    <span class="brand__square"></span>
    <span class="brand__name">Dulom</span>
  </div>
</section>

</body>
</html>
```